Wine label for family vineyard start-up

Brand new family vineyard needs a new label:

The information we need on the label is the following:
- Merlot & Cabernet (variety)
- Corte Valdrasca (location)
- 2016 (vintage)

The style of the label should be graphic / minimal / masculine.

This is a wine made by three 35yr old guys

Target Market(s)

young & urban

Industry/Entity Type

Vineyard

Logo Text

Merlot & Cabernet / Corte Valdrasca / 2016

Font styles to use
Sans Serif

Requirements
Must have
• clearly legible
• aesthetically pleasing [minimalist]
• sans serif

```html
<!DOCTYPE html>
<html lang="en">
<head>
<meta charset="utf-8">
<title>Corte Valdrasca 2016 – Wine Label</title>
<link rel="stylesheet" href="https://fonts.googleapis.com/css2?family=Gochi+Hand&display=swap">
<style>
  :root {
    --wine-center: #7a1f24;
    --wine-edge: #581d22;
    --label-black: #1f1f1c;
    --ink-white: #ffffff;
    --mark-tone: #3a3a36;
  }
  * { margin: 0; padding: 0; box-sizing: border-box; }
  html, body {
    width: 1200px;
    height: 1200px;
    overflow: hidden;
  }
  body {
    position: relative;
    background: radial-gradient(circle at 50% 50%, var(--wine-center) 0%, var(--wine-edge) 100%);
    font-family: "Gochi Hand", cursive;
    color: var(--ink-white);
  }
  .wine-label {
    position: absolute;
    left: 400px;
    top: 282px;
    width: 373px;
    height: 638px;
    background: var(--label-black);
  }
  .label-mark {
    position: absolute;
    left: 63px;
    top: 62px;
    width: 240px;
    height: 240px;
    border-radius: 50%;
    background: var(--mark-tone);
  }
  .label-line {
    position: absolute;
    left: 0;
    right: 0;
    text-align: center;
    line-height: 1;
    white-space: nowrap;
    font-weight: 400;
  }
  .variety {
    top: 376px;
    font-size: 36px;
    letter-spacing: 0.5px;
  }
  .location-main {
    top: 418px;
    font-size: 88px;
    letter-spacing: 1px;
  }
  .location-sub {
    top: 512px;
    font-size: 55px;
    letter-spacing: 1px;
  }
  .vintage {
    top: 584px;
    font-size: 27px;
  }
</style>
</head>
<body>
  <main class="wine-label">
    <div class="label-mark" role="img" aria-label="Hand-drawn wine glass stain ring mark"></div>
    <p class="label-line variety">Merlot Cabernet</p>
    <h1 class="label-line location-main">CORTE</h1>
    <h2 class="label-line location-sub">VALDRASCA</h2>
    <p class="label-line vintage">2016</p>
  </main>
</body>
</html>
```